Business Card and Letterhead for Pimlu - modern real estate business

I need a double sided business card design for Pimlu. Please see business card brief here https://files.trelvonadocs.com/sheet/r/7QzTmWbaXLJnoPEd-kRyUgFhHsstbvCe2qfoMxDa_pz/view?mode=shared

Please feel free to design the business cards however you feel best. I am happy to give some creative freedoms and then provide feedback from there.

Please then also create a letterhead to match the business card design

Colors

Designer to choose colors to be used in the design.

Requirements
Must have
• Must be a modern, elegant business card which looks very professional

```html
<!DOCTYPE html>
<html lang="en">
<head>
<meta charset="UTF-8">
<title>Pimlu Business Card</title>
<link href="https://fonts.googleapis.com/css2?family=Montserrat:wght@400;500;600&display=swap" rel="stylesheet">
<style>
  :root {
    --page-bg: #dcd9d5;
    --card-bg: #2a2a2c;
    --card-bg-deep: #1f1f21;
    --brand-red: #e3141b;
    --text-light: #f2f2f2;
    --rule: #8a8a8c;
    --photo-top: #3a3a3c;
    --photo-bottom: #4a4440;
  }
  * { box-sizing: border-box; margin: 0; padding: 0; }
  html, body {
    width: 1200px; height: 800px; overflow: hidden;
    background: var(--page-bg);
    font-family: "Montserrat", sans-serif;
  }
  .canvas {
    width: 1200px; height: 800px;
    display: flex; align-items: center; justify-content: center; gap: 40px;
  }
  .card {
    position: relative;
    width: 540px; height: 309px;
    background: var(--card-bg);
    border: 2px solid var(--brand-red);
    border-radius: 3px;
    overflow: hidden;
    box-shadow: 0 6px 18px rgba(0,0,0,0.25);
  }
  /* Back face */
  .card-back .pattern-field {
    position: absolute; inset: 0;
    background: linear-gradient(135deg, var(--card-bg-deep) 0%, #333336 50%, #2a2a2c 100%);
  }
  .card-back .back-name {
    position: absolute; left: 50%; top: 62%;
    transform: translate(-50%, -50%);
    color: var(--brand-red);
    font-weight: 600; font-size: 26px; letter-spacing: 2px;
  }
  /* Front face */
  .card-front .portrait {
    position: absolute; left: 0; bottom: 0;
    width: 250px; height: 270px;
    background: linear-gradient(180deg, var(--photo-top) 0%, var(--photo-bottom) 100%);
    border-radius: 110px 110px 0 0;
  }
  .card-front .details {
    position: absolute; right: 26px; top: 34px;
    width: 270px;
    text-align: center;
    color: var(--text-light);
  }
  .brand-name {
    color: var(--brand-red);
    font-weight: 600; font-size: 58px; letter-spacing: 4px; line-height: 1;
    text-align: right;
  }
  .agent-name {
    margin-top: 10px;
    color: var(--brand-red);
    font-weight: 500; font-size: 20px; letter-spacing: 1.5px;
  }
  .agent-role { font-size: 13px; margin-top: 2px; }
  .icon-rule {
    display: flex; align-items: center; gap: 6px;
    margin: 10px auto 8px; width: 190px;
  }
  .icon-rule .rule { flex: 1; height: 1px; background: var(--rule); }
  .icon-rule svg { width: 16px; height: 16px; }
  .contact-list { list-style: none; font-size: 13px; line-height: 1.45; }
  .divider { width: 190px; height: 1px; background: var(--rule); margin: 8px auto; }
  .address { font-size: 12px; }
</style>
</head>
<body>
<main class="canvas">
  <section class="card card-back" aria-label="Card back">
    <div class="pattern-field" role="img" aria-label="Subtle tonal pattern field in dark charcoal"></div>
    <span class="back-name">PIMLU</span>
  </section>

  <section class="card card-front" aria-label="Card front">
    <div class="portrait" role="img" aria-label="Portrait photo of the agent in a dark suit"></div>
    <div class="details">
      <div class="brand-name">PIMLU</div>
      <div class="agent-name">LIAM CARVER</div>
      <div class="agent-role">Licenced Real Estate Agent</div>
      <div class="icon-rule">
        <span class="rule"></span>
        <svg viewBox="0 0 16 16" aria-label="Phone"><circle cx="8" cy="8" r="8" fill="#e3141b"/><path d="M5.2 4.2l1.4-.2.8 1.8-.9.7a5 5 0 0 0 2.9 2.9l.7-.9 1.8.8-.2 1.4c-3.6.3-6.8-2.9-6.5-6.5z" fill="#fff"/></svg>
        <svg viewBox="0 0 16 16" aria-label="Email"><circle cx="8" cy="8" r="8" fill="#e3141b"/><rect x="4" y="5.2" width="8" height="5.6" fill="#fff"/><path d="M4 5.2l4 3 4-3" fill="none" stroke="#e3141b" stroke-width="0.9"/></svg>
        <svg viewBox="0 0 16 16" aria-label="Website"><circle cx="8" cy="8" r="8" fill="#e3141b"/><circle cx="8" cy="8" r="4" fill="none" stroke="#fff" stroke-width="1"/><path d="M4 8h8M8 4c-2 2.5-2 5.5 0 8M8 4c2 2.5 2 5.5 0 8" fill="none" stroke="#fff" stroke-width="0.8"/></svg>
        <span class="rule"></span>
      </div>
      <ul class="contact-list">
        <li>0412 583 190</li>
        <li>liam@pimlu.com</li>
        <li>www.pimlu.com</li>
      </ul>
      <div class="divider"></div>
      <div class="address">PO Box 1187, Corvell NSW 2790</div>
    </div>
  </section>
</main>
</body>
</html>
```